Harborlight Amusement Collective (HAC)

We need a business card design for Harborlight Amusement Collective. Modern and sleek looking, with all critical information. Open to single or double sided designs, if double sided info needs to be all on one side. The main Logo is Harborlight Amusement collective and must be on the card. The other three logos are for the brands that fall under the group, they might be good on the back.

Industry/Entity Type

Business

```html
<!DOCTYPE html>
<html lang="en">
<head>
<meta charset="utf-8">
<title>Harborlight Amusement Collective — Business Card</title>
<link rel="stylesheet" href="https://fonts.googleapis.com/css2?family=Montserrat:wght@500;600&family=Open+Sans:wght@400;600&display=swap">
<style>
  :root {
    --brand-blue: #2457a0;
    --brand-green: #86a03a;
    --band-grey: #ebebec;
    --ink: #4a4a4a;
    --paper: #ffffff;
    --backdrop: #e9e6e1;
  }
  * { box-sizing: border-box; margin: 0; padding: 0; }
  html, body { width: 1200px; height: 900px; overflow: hidden; }
  body {
    background: var(--backdrop);
    display: flex; align-items: center; justify-content: center; gap: 40px;
    font-family: "Open Sans", sans-serif;
  }
  .card {
    position: relative; width: 540px; height: 309px;
    background: var(--paper); overflow: hidden;
    box-shadow: 0 6px 18px rgba(0,0,0,.18);
  }
  /* Back side */
  .card-back .field {
    position: absolute; inset: 0 0 86px 0; background: var(--brand-blue);
    display: flex; align-items: center; justify-content: center; gap: 12px;
  }
  .wordmark {
    font-family: "Montserrat", sans-serif; font-weight: 600;
    letter-spacing: .04em; text-transform: uppercase;
  }
  .card-back .wordmark { color: var(--paper); font-size: 17px; }
  .mark-square { width: 22px; height: 22px; background: var(--brand-green); flex: none; }
  .brand-band {
    position: absolute; left: 0; right: 0; bottom: 0; height: 86px;
    background: var(--band-grey);
    display: flex; align-items: center; justify-content: space-around; padding: 0 14px;
  }
  .sub-brand {
    display: flex; align-items: center; gap: 6px;
    font-family: "Montserrat", sans-serif; font-weight: 600; font-size: 14px;
  }
  .sub-brand .dot { width: 14px; height: 14px; border-radius: 50%; }
  .sub-brand.terrace { color: #1f2a3a; } .sub-brand.terrace .dot { background: #1f2a3a; }
  .sub-brand.pierline { color: var(--brand-blue); } .sub-brand.pierline .dot { background: var(--brand-green); }
  .sub-brand.seatmark { color: var(--brand-blue); } .sub-brand.seatmark .dot { background: var(--brand-blue); }
  /* Front side */
  .swoosh { position: absolute; inset: 0; }
  .holder { position: absolute; left: 34px; top: 58px; }
  .holder-name {
    font-family: "Montserrat", sans-serif; font-weight: 500; font-size: 18px;
    letter-spacing: .02em; color: var(--brand-blue);
  }
  .holder-name .surname { color: var(--brand-green); }
  .holder-role { font-size: 12px; color: var(--ink); margin-top: 1px; }
  .contact { position: absolute; left: 34px; top: 140px; color: var(--ink); font-size: 13px; line-height: 18px; list-style: none; }
  .contact li { display: flex; align-items: center; gap: 7px; }
  .contact svg { width: 11px; height: 11px; fill: var(--brand-blue); flex: none; }
  .contact .address { margin-top: 6px; line-height: 20px; font-size: 13.5px; }
  .front-mark {
    position: absolute; right: 26px; top: 38px; width: 220px;
    display: flex; flex-direction: column; align-items: center; gap: 10px; text-align: center;
  }
  .front-mark .wordmark { color: var(--brand-blue); font-size: 15px; line-height: 20px; }
  .website {
    position: absolute; right: 22px; bottom: 108px;
    color: var(--paper); font-size: 11px;
  }
</style>
</head>
<body>
  <section class="card card-back" aria-label="Card back">
    <div class="field">
      <span class="mark-square"></span>
      <span class="wordmark">Harborlight Amusement Collective</span>
    </div>
    <div class="brand-band">
      <span class="sub-brand terrace"><span class="dot"></span>Terrace Hospitality</span>
      <span class="sub-brand pierline"><span class="dot"></span>Pierline Tickets</span>
      <span class="sub-brand seatmark"><span class="dot"></span>seatmark</span>
    </div>
  </section>

  <section class="card card-front" aria-label="Card front">
    <svg class="swoosh" viewBox="0 0 540 309" preserveAspectRatio="none" aria-hidden="true">
      <path d="M0 262 C120 268 250 230 380 175 C440 150 500 130 540 118 L540 309 L0 309 Z" fill="var(--brand-green)"/>
      <path d="M0 280 C140 282 260 240 380 188 C440 162 500 140 540 128 L540 309 L0 309 Z" fill="var(--paper)"/>
      <path d="M0 286 C140 288 260 246 380 194 C440 168 500 146 540 134 L540 309 L0 309 Z" fill="var(--brand-blue)"/>
    </svg>

    <div class="holder">
      <h1 class="holder-name">DANIEL <span class="surname">REYES</span></h1>
      <p class="holder-role">Managing Director</p>
    </div>

    <ul class="contact">
      <li><svg viewBox="0 0 16 16"><path d="M3 1l3 3-2 2c1 2 3 4 5 5l2-2 3 3-2 3C6 14 2 10 1 3z"/></svg>(044) 555 0147</li>
      <li><svg viewBox="0 0 16 16"><path d="M4 0h8v16H4zM5.5 2v10h5V2zM7 13h2v1.5H7z"/></svg>(044) 555 0148</li>
      <li><svg viewBox="0 0 16 16"><path d="M0 3h16v10H0zM1.5 4.5v.5L8 9l6.5-4v-.5z"/></svg>hello@harborlightac.com</li>
      <li class="address">1234, Address Goes Here,<br>Country, 12345</li>
    </ul>

    <div class="front-mark">
      <span class="mark-square"></span>
      <span class="wordmark">Harborlight Amusement Collective</span>
    </div>

    <p class="website">www.harborlightac.com</p>
  </section>
</body>
</html>
```